Business card por a urban DJ, up scale audience target

Need a sober design, modern, conservative colors but i can consider some options, y play rnb, hip hop, EDM and top40.

Business card for contact and personal info, double sided, use logo attrached please; im 42 so i need a card acording to my age an target audience.

Target Market(s)

Adult people, up scale audience

Industry/Entity Type

Music Download

Contact Information for Business Card

Cel (318) 4207265518 www.lumadrift.com

Requirements
Must have
• open mind
Nice to have
• open mind
Should not have
• DJ

```html
<!DOCTYPE html>
<html lang="en">
<head>
<meta charset="utf-8">
<title>Lumadrift business card</title>
<link rel="stylesheet" href="https://fonts.googleapis.com/css2?family=Open+Sans:wght@400;700;800&display=swap">
<style>
  :root {
    --page: #2b2b2b;
    --card: #000000;
    --ink: #c6c6c6;
    --ink-soft: #a9a9a9;
  }
  * { margin: 0; padding: 0; box-sizing: border-box; }
  html, body { width: 1200px; height: 900px; overflow: hidden; }
  body {
    background: var(--page);
    font-family: "Open Sans", Arial, sans-serif;
    position: relative;
  }
  .card {
    position: absolute;
    left: 240px;
    width: 720px;
    height: 412px;
    background: var(--card);
    overflow: hidden;
  }
  .card--front { top: 24px; }
  .card--back { top: 464px; }
  .card svg { position: absolute; inset: 0; }
  .wordmark {
    position: absolute;
    color: var(--ink);
    font-weight: 800;
    letter-spacing: 2px;
    line-height: 1;
  }
  .card--front .wordmark { left: 300px; top: 70px; font-size: 118px; }
  .front-url {
    position: absolute;
    left: 312px;
    top: 208px;
    color: var(--ink);
    font-size: 19px;
    letter-spacing: 5px;
  }
  .card--back .wordmark { left: 34px; top: 44px; font-size: 92px; }
  .contact {
    position: absolute;
    left: 34px;
    top: 292px;
    color: var(--ink);
  }
  .contact__name { font-size: 21px; font-weight: 700; }
  .contact__role { font-size: 12px; color: var(--ink-soft); margin-top: 1px; }
  .contact__rule { width: 170px; height: 1px; background: var(--ink-soft); margin: 7px 0 6px; }
  .contact__line {
    display: flex; align-items: center; gap: 7px;
    font-size: 13px; line-height: 19px;
  }
  .contact__line svg { position: static; width: 11px; height: 11px; }
</style>
</head>
<body>

<section class="card card--front">
  <svg viewBox="0 0 720 412" width="720" height="412" aria-hidden="true">
    <g fill="#c6c6c6">
      <rect x="0" y="382" width="8" height="30"/><rect x="12" y="390" width="8" height="22"/>
      <rect x="24" y="404" width="8" height="8"/><rect x="36" y="386" width="8" height="26"/>
      <rect x="48" y="394" width="8" height="18"/><rect x="60" y="378" width="8" height="34"/>
      <rect x="72" y="402" width="8" height="10"/><rect x="84" y="408" width="8" height="4"/>
      <rect x="96" y="408" width="8" height="4"/><rect x="108" y="400" width="8" height="12"/>
      <rect x="120" y="392" width="8" height="20"/><rect x="132" y="404" width="8" height="8"/>
      <rect x="144" y="386" width="8" height="26"/><rect x="156" y="398" width="8" height="14"/>
      <rect x="168" y="408" width="8" height="4"/><rect x="180" y="402" width="8" height="10"/>
      <rect x="192" y="394" width="8" height="18"/><rect x="204" y="382" width="8" height="30"/>
      <rect x="216" y="400" width="8" height="12"/><rect x="228" y="408" width="8" height="4"/>
      <rect x="240" y="396" width="8" height="16"/><rect x="252" y="404" width="8" height="8"/>
      <rect x="264" y="386" width="8" height="26"/><rect x="276" y="402" width="8" height="10"/>
      <rect x="288" y="408" width="8" height="4"/><rect x="300" y="404" width="8" height="8"/>
      <rect x="312" y="398" width="8" height="14"/><rect x="324" y="390" width="8" height="22"/>
      <rect x="336" y="406" width="8" height="6"/><rect x="348" y="408" width="8" height="4"/>
      <rect x="360" y="400" width="8" height="12"/><rect x="372" y="394" width="8" height="18"/>
      <rect x="384" y="404" width="8" height="8"/><rect x="396" y="408" width="8" height="4"/>
      <rect x="408" y="398" width="8" height="14"/><rect x="420" y="386" width="8" height="26"/>
      <rect x="432" y="402" width="8" height="10"/><rect x="444" y="406" width="8" height="6"/>
      <rect x="456" y="396" width="8" height="16"/><rect x="468" y="404" width="8" height="8"/>
    </g>
  </svg>
  <div class="wordmark">LUMA</div>
  <div class="front-url">www.lumadrift.com</div>
</section>

<section class="card card--back">
  <svg viewBox="0 0 720 412" width="720" height="412" aria-hidden="true">
    <line x1="200" y1="228" x2="720" y2="228" stroke="#a9a9a9" stroke-width="1.5"/>
    <g fill="#c6c6c6">
      <rect x="352" y="292" width="8" height="8"/><rect x="364" y="282" width="8" height="18"/>
      <rect x="376" y="288" width="8" height="12"/><rect x="388" y="296" width="8" height="4"/>
      <rect x="400" y="290" width="8" height="10"/><rect x="412" y="280" width="8" height="20"/>
      <rect x="424" y="294" width="8" height="6"/><rect x="436" y="296" width="8" height="4"/>
      <rect x="448" y="286" width="8" height="14"/><rect x="460" y="296" width="8" height="4"/>
      <rect x="472" y="288" width="8" height="12"/><rect x="484" y="276" width="8" height="24"/>
      <rect x="496" y="284" width="8" height="16"/><rect x="508" y="294" width="8" height="6"/>
      <rect x="520" y="284" width="8" height="16"/><rect x="532" y="270" width="8" height="30"/>
      <rect x="544" y="280" width="8" height="20"/><rect x="556" y="290" width="8" height="10"/>
      <rect x="568" y="294" width="8" height="6"/><rect x="580" y="296" width="8" height="4"/>
      <rect x="592" y="284" width="8" height="16"/><rect x="604" y="276" width="8" height="24"/>
      <rect x="616" y="288" width="8" height="12"/><rect x="628" y="270" width="8" height="30"/>
      <rect x="640" y="284" width="8" height="16"/><rect x="652" y="264" width="8" height="36"/>
      <rect x="664" y="254" width="8" height="46"/><rect x="676" y="268" width="8" height="32"/>
      <rect x="688" y="244" width="8" height="56"/>
    </g>
  </svg>
  <div class="wordmark">LUMA</div>
  <div class="contact">
    <div class="contact__name">Marco Vell</div>
    <div class="contact__role">CEO</div>
    <div class="contact__rule"></div>
    <div class="contact__line">
      <svg viewBox="0 0 12 12" aria-hidden="true"><rect x="3" y="0.5" width="6" height="11" rx="1" fill="none" stroke="#c6c6c6" stroke-width="1.2"/><rect x="5" y="9" width="2" height="1" fill="#c6c6c6"/></svg>
      <span>(318) 4207265518</span>
    </div>
    <div class="contact__line">
      <svg viewBox="0 0 12 12" aria-hidden="true"><circle cx="6" cy="6" r="5" fill="none" stroke="#c6c6c6" stroke-width="1.2"/><ellipse cx="6" cy="6" rx="2" ry="5" fill="none" stroke="#c6c6c6" stroke-width="1"/><line x1="1" y1="6" x2="11" y2="6" stroke="#c6c6c6" stroke-width="1"/></svg>
      <span>www.lumadrift.com</span>
    </div>
  </div>
</section>

</body>
</html>
```